Classy, Elegant, Simple Business Card Design

Looking to have a classy, simple, and elegant design. Want a top notch designed business card. I really like the look of the new torvane credit card. I also like the design I attached. I am trying to reach 21-29 year old females for booking us for there wedding or event. We offer Disc Jockey Service, Photo Booth Rentals, and Uplighting .

Target Market(s)

21-28 year old females

Contact Information for Business Card

Has to have logo, website, email, and phone number

Font styles to use
Other font styles liked:
• open to font choice, modern, clean
Designer to choose
33a6d7
0791cd
0555a3
ffffff

Requirements
Must have
• Has to have logo, website, email, and phone number
Nice to have
• I really like the design of the new torvane credit card. I also included my logo and some designs I like
Should not have
• clutter or too much info

```html
<!DOCTYPE html>
<html lang="en">
<head>
<meta charset="utf-8">
<title>Brightline Events – Business Card</title>
<link href="https://fonts.googleapis.com/css2?family=Montserrat:wght@400;700&display=swap" rel="stylesheet">
<style>
  :root {
    --backdrop: #2b2e33;
    --navy: #0e2f5f;
    --navy-deep: #0a2550;
    --navy-light: #1d5394;
    --sky: #33a6d7;
    --azure: #0791cd;
    --royal: #0555a3;
    --paper: #ffffff;
    --ink-soft: #8a8f96;
  }
  html, body {
    margin: 0;
    padding: 0;
    width: 1200px;
    height: 900px;
    overflow: hidden;
    background: var(--backdrop);
    font-family: "Montserrat", sans-serif;
  }
  .canvas {
    position: relative;
    width: 1200px;
    height: 900px;
    display: flex;
    align-items: center;
    justify-content: center;
    gap: 60px;
  }
  .card {
    width: 490px;
    height: 280px;
    border-radius: 6px;
    overflow: hidden;
    box-shadow: 0 18px 40px rgba(0,0,0,0.45);
    position: relative;
  }
  .card svg { display: block; }

  /* front */
  .card-front { background: var(--paper); }
  .card-front .contact {
    position: absolute;
    left: 34px;
    top: 40px;
  }
  .contact .person-name {
    margin: 0 0 14px;
    font-weight: 700;
    font-size: 21px;
    letter-spacing: 0.5px;
    color: var(--azure);
  }
  .contact .line {
    display: flex;
    align-items: center;
    gap: 9px;
    margin: 0 0 6px;
    font-size: 13px;
    color: var(--ink-soft);
  }
  .contact .line svg { flex: none; }

  .brand-name {
    position: absolute;
    margin: 0;
    font-weight: 700;
    color: var(--sky);
    white-space: nowrap;
    text-align: center;
  }
  .card-front .brand-name {
    left: 236px;
    width: 244px;
    top: 168px;
    font-size: 18px;
    letter-spacing: 1px;
  }

  /* back */
  .card-back { background: var(--navy); }
  .card-back .pattern {
    position: absolute;
    inset: 0;
  }
  .card-back .brand-name {
    left: 0;
    right: 0;
    top: 122px;
    font-size: 30px;
    letter-spacing: 1.5px;
  }
</style>
</head>
<body>
<main class="canvas">

  <section class="card card-front" aria-label="Business card front">
    <svg width="490" height="280" viewBox="0 0 490 280" aria-hidden="true">
      <path class="accent-arc" d="M215 270 A 250 250 0 0 1 430 22" fill="none" stroke="var(--azure)" stroke-width="5" stroke-linecap="round"/>
      <circle class="brand-disc" cx="430" cy="250" r="230" fill="var(--navy)"/>
    </svg>

    <div class="contact">
      <h1 class="person-name">DANA MERROW</h1>
      <p class="line">
        <svg width="12" height="12" viewBox="0 0 24 24" aria-hidden="true"><path fill="var(--royal)" d="M6.6 10.8a15 15 0 0 0 6.6 6.6l2.2-2.2c.3-.3.7-.4 1-.2 1.1.4 2.3.6 3.6.6.6 0 1 .4 1 1V20c0 .6-.4 1-1 1A17 17 0 0 1 3 4c0-.6.4-1 1-1h3.5c.6 0 1 .4 1 1 0 1.3.2 2.5.6 3.6.1.3 0 .7-.2 1z"/></svg>
        0000 542 718
      </p>
      <p class="line">
        <svg width="12" height="12" viewBox="0 0 24 24" aria-hidden="true"><rect x="2" y="5" width="20" height="14" rx="1.5" fill="var(--royal)"/><path d="M3 6l9 7 9-7" fill="none" stroke="#fff" stroke-width="1.8"/></svg>
        hello@brightline.com
      </p>
      <p class="line">
        <svg width="12" height="12" viewBox="0 0 24 24" aria-hidden="true"><circle cx="12" cy="12" r="10" fill="var(--royal)"/><path d="M2 12h20M12 2c3 3 3 17 0 20M12 2c-3 3-3 17 0 20" fill="none" stroke="#fff" stroke-width="1.4"/></svg>
        www.brightline.com
      </p>
    </div>

    <p class="brand-name">BRIGHTLINE EVENTS</p>
  </section>

  <section class="card card-back" aria-label="Business card back">
    <svg class="pattern" width="490" height="280" viewBox="0 0 490 280" role="img" aria-label="Radiating mosaic of soft blue squares fanning out behind the brand name">
      <defs>
        <radialGradient id="mosaicGlow" cx="0.5" cy="0.45" r="0.75">
          <stop offset="0" stop-color="var(--navy-deep)"/>
          <stop offset="0.45" stop-color="var(--navy)"/>
          <stop offset="1" stop-color="var(--navy-light)"/>
        </radialGradient>
      </defs>
      <rect width="490" height="280" fill="url(#mosaicGlow)"/>
    </svg>
    <p class="brand-name">BRIGHTLINE EVENTS</p>
  </section>

</main>
</body>
</html>
```